Local Flower Farm Needs Business Card Design

I need business cards designed for a flower farm based in Eudora, Kansas.
Business Info:
We are a local cut flower farm located in Eudora, Kansas, founded by Corinne Haldwick. What started as a passion for agriculture and search for more joy in daily life has blossomed into a small business dedicated to providing the community with beautiful, fresh, and sustainable flowers. We specialize in local, seasonal blooms, ensuring that every petal reflects the care and dedication we pour into our craft. Our mission is to deliver the highest quality flowers directly to our customers through local farmers markets and to florists who share our commitment to sustainability. Join us in celebrating the beauty of nature, one bloom at a time!
Contact Details:
Corinne Haldwick
Owner
Phone 913-555-0147
Facebook: Rosalind Thorpe Gardens
Instagram: @RosalindThorpeGardens
Website: RosalindThorpeGardens.example
Target Market(s)
Wholesale to Florists and Direct to Consumer via Farmers Market
Industry/Entity Type
Florist, Farm
Contact Information for Business Card
Name, Contact Info, Logo
Look and feel
Each slider illustrates characteristics of the customer's brand and the style your logo design should communicate.

```html
<!DOCTYPE html>
<html lang="en">
<head>
<meta charset="utf-8">
<title>Rosalind Thorpe Gardens — Business Card</title>
<link href="https://fonts.googleapis.com/css2?family=Libre+Baskerville:wght@400;700&display=swap" rel="stylesheet">
<style>
  :root {
    --stage: #1c1c1e;
    --paper: #ffffff;
    --teal: #0c2a30;
    --teal-ink: #123a42;
    --on-teal: #eef3f2;
    --rule: #5f7a7e;
  }
  * { box-sizing: border-box; margin: 0; padding: 0; }
  html, body { width: 1200px; height: 1200px; overflow: hidden; }
  body {
    background: var(--stage);
    font-family: "Libre Baskerville", Georgia, serif;
    display: flex;
    flex-direction: column;
    align-items: center;
    justify-content: center;
    gap: 60px;
  }
  .card {
    width: 840px;
    height: 480px;
    background: var(--paper);
    position: relative;
    overflow: hidden;
    box-shadow: 0 18px 40px rgba(0,0,0,.45);
  }
  .brand-mark {
    width: 250px;
    height: 250px;
    border: 1.5px solid var(--rule);
    border-radius: 50%;
    display: flex;
    align-items: center;
    justify-content: center;
    text-align: center;
    color: var(--teal-ink);
    font-size: 22px;
    line-height: 1.45;
    letter-spacing: .12em;
    text-transform: uppercase;
    padding: 30px;
  }
  .card--front .brand-mark {
    position: absolute;
    left: 50%;
    top: 62px;
    transform: translateX(-50%);
  }
  .web-line {
    position: absolute;
    left: 0; right: 0;
    bottom: 74px;
    text-align: center;
    color: var(--teal-ink);
    font-size: 18px;
    letter-spacing: .26em;
    text-transform: uppercase;
  }
  .card--back { display: flex; }
  .back-brand {
    width: 48%;
    display: flex;
    align-items: center;
    justify-content: center;
  }
  .back-details {
    flex: 1;
    background: var(--teal);
    color: var(--on-teal);
    padding: 70px 40px 0 48px;
  }
  .person-name {
    font-size: 27px;
    letter-spacing: .09em;
    text-transform: uppercase;
    font-weight: 400;
  }
  .person-role {
    font-size: 18px;
    letter-spacing: .03em;
    margin-top: 6px;
  }
  .contact-list {
    list-style: none;
    margin-top: 62px;
    display: flex;
    flex-direction: column;
    gap: 9px;
  }
  .contact-item {
    display: flex;
    align-items: center;
    gap: 12px;
    font-size: 19px;
    white-space: nowrap;
  }
  .contact-icon {
    width: 24px; height: 24px;
    flex: none;
  }
</style>
</head>
<body>
  <section class="card card--front">
    <div class="brand-mark">Rosalind Thorpe Gardens</div>
    <p class="web-line">www.rosalindthorpegardens.example</p>
  </section>

  <section class="card card--back">
    <div class="back-brand">
      <div class="brand-mark">Rosalind Thorpe Gardens</div>
    </div>
    <div class="back-details">
      <h1 class="person-name">Corinne Haldwick</h1>
      <p class="person-role">Owner</p>
      <ul class="contact-list">
        <li class="contact-item">
          <svg class="contact-icon" viewBox="0 0 24 24" aria-hidden="true">
            <circle cx="12" cy="12" r="11" fill="none" stroke="#eef3f2" stroke-width="1.4"/>
            <path d="M9 6.5c-.8.3-1.6 1.2-1.5 2.3.3 3.6 4.1 7.7 7.8 8.2 1 .1 1.9-.6 2.2-1.4l-2.2-1.6-1.2 1c-1.5-.7-3-2.3-3.6-3.8l1-1.2L9 6.5z" fill="#eef3f2"/>
          </svg>
          913-555-0147
        </li>
        <li class="contact-item">
          <svg class="contact-icon" viewBox="0 0 24 24" aria-hidden="true"><circle cx="12" cy="12" r="11" fill="none" stroke="#eef3f2" stroke-width="1.4"/></svg>
          Rosalind Thorpe Gardens
        </li>
        <li class="contact-item">
          <svg class="contact-icon" viewBox="0 0 24 24" aria-hidden="true"><circle cx="12" cy="12" r="11" fill="none" stroke="#eef3f2" stroke-width="1.4"/></svg>
          @RosalindThorpeGardens
        </li>
        <li class="contact-item">
          <svg class="contact-icon" viewBox="0 0 24 24" aria-hidden="true"><circle cx="12" cy="12" r="11" fill="none" stroke="#eef3f2" stroke-width="1.4"/></svg>
          RosalindThorpeGardens.example
        </li>
      </ul>
    </div>
  </section>
</body>
</html>
```